WordPress Website for BidLinks Agency

We are in need of a complete WordPress design.

We will be seeking new clients and we want them to have a great idea of what our business does when they get to the page along with the products and services we offer. Our current website is www.mossyharbor.com and it really needs an upgrade. Wordpress would be great but our owner knows HTML as well so he can go in and edit things later if need be. Please apply if you can show what a Search Engine Marketing company does and can explain this information to a lay person. Also, the website should be responsive so it fits mobile, tablet, and desktop settings while changing to these different widths.

Also, we are not an SEO company, per se but an SEM / PPC company that operates on Zorvic BidLinks, Plim Promos, Chatterwall Promos, and other PPC platforms.

Themes are fine just as long as the content and the visuals display what a search engine marketing company does. Really looking for clients to know exactly why a search engine marketing company does when the get to the site, why they should use a search engine marketing company, and the best way to contact us to get a quote.

Here are some other search engine marketing sites that I like in terms of the content and the layout to give an idea of what should be included on the site:
http://www.fendowlabs.com/
http://www.k9rworks.com/
http://www.boulderpartners.com/
http://www.vjnpromo.com/
http://www.halvorteam.com/
http://meetthepinecrew.com/

Please include my new phone number of the website: 866-555-0142.

Thank you, 
Walt 

Target Market(s)

We are a search engine marketing company looking for more clients and want to be able to explain what a search engine marketing company does in layman's terms.

Industry/Entity Type

Marketing

Font styles to use
Sans Serif

Requirements
Must have
• About Us Page
Services Page
Home Page
Success Stories Page
Blog
Social Media links / feeds
Visuals of products / services offered
Jobs page
Nice to have
• Responsive design
Client Login / Space on the site for monthly client payments / Link to CoinTap or Rivermoss

```html
<!DOCTYPE html>
<html lang="en">
<head>
<meta charset="utf-8">
<title>Mossy Harbor Digital Marketing</title>
<link href="https://fonts.googleapis.com/css2?family=Arimo:wght@400;700&display=swap" rel="stylesheet">
<style>
:root{
  --red:#e8212b;
  --ink:#333;
  --muted:#555;
  --white:#fff;
  --welcome-bg:#dedede;
  --products-bg:#c9c9c9;
  --widgets-bg:#e3e3e3;
  --footer-bg:#333;
  --chirp:#5ccff5;
  --friend:#1d63b7;
}
*{margin:0;padding:0;box-sizing:border-box}
html,body{width:900px;height:1200px;overflow:hidden}
body{font-family:"Arimo",Arial,sans-serif;color:var(--ink);background:var(--white);position:relative}
.abs{position:absolute}
.top-bar{left:0;top:0;width:900px;height:8px;background:var(--red)}
.header{left:0;top:8px;width:900px;height:84px;background:var(--white);border-bottom:1px solid #ccc}
.brand{left:150px;top:46px;display:flex;align-items:center;gap:6px;font-size:19px;font-weight:700;color:var(--red)}
.brand-dot{width:14px;height:14px;border-radius:50%;background:var(--red)}
.phone{left:514px;top:16px;font-size:8.5px;font-weight:700;display:flex;align-items:center;gap:5px}
.search{left:610px;top:6px;width:139px;height:21px;border:1px solid #ccc;font-size:7px;color:#aaa;padding:6px 10px}
.search svg{position:absolute;right:6px;top:3px}
.nav{left:521px;top:54px;display:flex;gap:19px;font-size:8.5px}
.nav-active{left:517px;top:82px;width:37px;height:3px;background:var(--red)}
.hero{left:0;top:92px;width:900px;height:318px;background:linear-gradient(180deg,#a9bccb 0%,#7f9a58 35%,#6f8a3a 70%,#8a8226 100%)}
.hero-person{left:560px;top:110px;width:192px;height:300px;background:linear-gradient(180deg,#c9b39f,#a9bcd6 40%,#9eb2cd);border-radius:40px 40px 0 0;opacity:.85}
.hero-title{left:168px;top:200px;font-size:21px;font-weight:700;color:var(--red)}
.hero-sub{left:169px;top:233px;font-size:14px;font-weight:700;color:#111}
.hero-arrow{top:226px}
.dots{left:433px;top:390px;display:flex;gap:2px}
.dots span{width:9px;height:9px;border-radius:50%;border:2px solid #fff;background:#222}
.dots span.on{background:var(--red)}
.welcome{left:0;top:410px;width:900px;height:100px;background:var(--welcome-bg);text-align:center}
.section-title{font-size:14.5px;color:var(--red);font-weight:400}
.welcome h2{margin-top:16px}
.welcome p{width:585px;margin:12px auto 0;font-size:7px;line-height:10.7px;color:var(--muted)}
.products{left:0;top:510px;width:900px;height:254px;background:var(--products-bg)}
.products h2{position:absolute;left:0;width:900px;top:12px;text-align:center}
.pager{font-size:10px;font-weight:700;color:#111;letter-spacing:2px}
.card{top:44px;width:171px;height:188px;background:#f6f6f6;border:1px solid #ddd;border-bottom:3px solid var(--red)}
.card-img{position:absolute;left:5px;top:6px;width:160px;height:86px}
.card h3{position:absolute;left:5px;top:100px;font-size:11px;font-weight:400;color:var(--red)}
.card p{position:absolute;left:6px;top:122px;width:160px;font-size:7px;line-height:8.6px;color:var(--muted)}
.card a{position:absolute;left:6px;top:171px;font-size:6.5px;color:#111;text-decoration:none}
.widgets{left:0;top:764px;width:900px;height:356px;background:var(--widgets-bg)}
.widget{top:26px;width:171px;height:185px;background:var(--white);border:1px solid #ccc}
.widget-head{height:22px;color:#fff;font-size:10px;display:flex;align-items:center;justify-content:center;gap:6px;position:relative}
.news .widget-head{background:var(--red)}
.news .widget-head .pager{position:absolute;right:8px;top:6px;color:#fff;font-size:8px}
.news-item{margin:12px 6px 0;font-size:7px;line-height:8.6px;color:var(--muted);padding-bottom:8px}
.news-item+.news-item{border-top:1px dotted #bbb;padding-top:12px;margin-top:0}
.news-item b{display:block;margin-top:7px;color:#111;font-weight:400;font-size:6.5px}
.chirp .widget-head{background:var(--chirp)}
.chirp-scroll{position:absolute;right:0;top:22px;width:5px;height:162px;background:#777}
.chirp-scroll span{display:block;height:24px;background:var(--chirp)}
.tweet{display:flex;gap:7px;margin:6px 10px 0 10px;padding-bottom:5px;border-bottom:1px solid #ddd;font-size:6.5px;line-height:9px;color:#777}
.tweet:last-of-type{border-bottom:0}
.tweet-dot{width:7px;height:7px;border-radius:50%;background:#222;margin-top:2px;flex:none}
.tweet em{font-style:normal;color:#a3291f}
.tweet-meta{color:#111;margin-top:3px}
.friend .widget-head{background:var(--friend);justify-content:center}
.fb-sq{width:7px;height:9px;background:#fff}
.fb-bar{display:flex;align-items:center;gap:10px;padding:7px 12px;font-size:7px;border-bottom:1px solid #ddd}
.fb-bar b{color:var(--red);font-weight:400}
.like{background:#4a86d8;color:#fff;padding:2px 4px;font-size:6px}
.fb-count{color:var(--friend)}
.fb-scroll{position:absolute;right:0;top:47px;width:5px;height:138px;background:#777}
.fb-scroll span{display:block;height:24px;background:var(--friend)}
.fb-post{display:flex;gap:8px;margin:12px 12px 0 9px;padding-bottom:8px;border-bottom:1px solid #ddd;font-size:6.8px;line-height:8.4px;color:#444}
.fb-post .mini{width:50px;flex:none;font-size:6px;color:var(--red);margin-top:8px}
.fb-post .who{text-align:right;margin-top:8px;color:#111}
.fb-foot{position:absolute;left:10px;bottom:3px;font-size:6px;color:var(--friend)}
.clients-pager{left:713px;top:232px}
.clients{left:150px;top:250px;width:600px;height:80px;background:#ddd;border:1px solid #ccc;display:flex;align-items:center;justify-content:space-around}
.client{display:flex;align-items:center;gap:8px;font-size:18px;color:#444}
.client i{width:22px;height:22px;display:block}
.footer{left:0;top:1120px;width:900px;height:80px;background:var(--footer-bg);color:#fff}
.footer-links{position:absolute;left:150px;top:29px;font-size:7.5px}
.footer-links b{font-weight:700}
.copy{position:absolute;left:151px;top:47px;font-size:7px}
.social{position:absolute;left:658px;top:26px;display:flex;gap:3px}
.social span{width:21px;height:21px;border-radius:50%}
</style>
</head>
<body>
<div class="abs top-bar"></div>
<header class="abs header">
  <div class="abs brand"><span class="brand-dot"></span>MossyHarbor</div>
  <div class="abs phone">
    <svg width="12" height="10" viewBox="0 0 12 10"><path d="M1 3c0-2 10-2 10 0v1H8V3H4v1H1z M3 5h6l2 4H1z" fill="#222"/></svg>
    +91 555 010 2233
  </div>
  <div class="abs search">Search
    <svg width="14" height="14" viewBox="0 0 14 14"><circle cx="6" cy="6" r="4.5" fill="none" stroke="#888" stroke-width="1.5"/><path d="M9.5 9.5L13 13" stroke="#888" stroke-width="1.6"/></svg>
  </div>
  <nav class="abs nav"><span>Home</span><span>Success Stories</span><span>About Us</span><span>Contact Us</span></nav>
  <div class="abs nav-active" style="top:82px"></div>
</header>

<section class="abs hero" role="img" aria-label="Blurred green countryside backdrop with a smiling man in a light blue shirt holding a laptop"></section>
<div class="abs hero-person" role="img" aria-label="Man in a light blue shirt holding a laptop"></div>
<h1 class="abs hero-title">Mossy Harbor Digital Marketing</h1>
<p class="abs hero-sub">Experts in Explosive Advertising</p>
<svg class="abs hero-arrow" style="left:22px" width="14" height="18" viewBox="0 0 14 18"><path d="M11 2L4 9l7 7" fill="none" stroke="#fff" stroke-width="3.5"/></svg>
<svg class="abs hero-arrow" style="left:856px" width="14" height="18" viewBox="0 0 14 18"><path d="M3 2l7 7-7 7" fill="none" stroke="#fff" stroke-width="3.5"/></svg>
<div class="abs dots"><span class="on"></span><span></span><span></span></div>

<section class="abs welcome">
  <h2 class="section-title">Welcome MossyHarbor</h2>
  <p>Mossy Harbor Digital Marketing was founded in 2011 by Walt Brenner. After spending a couple years working in his dad's insurance agency, he began to notice that lots of his dad's clients were small business owners and needed an online presence. At this point, Walt learned as much as he could about building websites and this eventually led to him learning more about marketing on Friendbook and Zorvic. Walt's first client was a neighborhood barber where he bartered the design of a website in exchange for haircuts. Looking nice and fresh, Walt has gone on to help lots of businesses expand their digital marketing and attract customers using tools like Zorvic BidLinks and Chatterwall Promos.</p>
</section>

<section class="abs products">
  <h2 class="section-title">Our Products</h2>
  <div class="abs pager" style="left:736px;top:14px">‹ ›</div>
  <article class="abs card" style="left:165px">
    <div class="card-img" role="img" aria-label="Hand drawing a marketing mind map on a green chalkboard" style="background:linear-gradient(135deg,#2f5a46,#1f4234)"></div>
    <h3>Marketing</h3>
    <p>Lorem ipsum dolor sit amet, consectetur adipiscing elit. Cras consectetur orci mollis arcu dapibus blandit iaculis urna sodales. Praesent convallis nunc lectus, in interdum ligula. Fusce ac neque arcu.</p>
    <a href="#">Link to somewhere..</a>
  </article>
  <article class="abs card" style="left:363px">
    <div class="card-img" role="img" aria-label="Open hands holding glowing network icons" style="background:linear-gradient(135deg,#d9dde0,#6e7378)"></div>
    <h3>Ideas</h3>
    <p>Lorem ipsum dolor sit amet, consectetur adipiscing elit. Cras consectetur orci mollis arcu dapibus blandit iaculis urna sodales. Praesent convallis nunc lectus, in interdum ligula. Fusce ac neque arcu.</p>
    <a href="#">Link to somewhere..</a>
  </article>
  <article class="abs card" style="left:562px">
    <div class="card-img" role="img" aria-label="Hand writing a digital marketing word cloud on a blue board" style="background:linear-gradient(135deg,#1a2f6b,#3a4f96)"></div>
    <h3>Digital marketing</h3>
    <p>Lorem ipsum dolor sit amet, consectetur adipiscing elit. Cras consectetur orci mollis arcu dapibus blandit iaculis urna sodales. Praesent convallis nunc lectus, in interdum ligula. Fusce ac neque arcu.</p>
    <a href="#">Link to somewhere..</a>
  </article>
</section>

<section class="abs widgets">
  <div class="abs widget news" style="left:166px">
    <div class="widget-head">News<span class="pager">‹ ›</span></div>
    <div class="news-item">Lorem ipsum dolor sit amet, consectetur adipiscing elit. Cras consectetur orci mollis arcu dapibus blandit iaculis urna sodales. Praesent convallis nunc lectus, in interdum ligula. Fusce ac neque arcu.<b>Learn more&gt;&gt;</b></div>
    <div class="news-item">Lorem ipsum dolor sit amet, consectetur adipiscing elit. Cras consectetur orci mollis arcu dapibus blandit iaculis urna sodales. Praesent convallis nunc lectus, in interdum ligula. Fusce ac neque arcu.<b>Learn more&gt;&gt;</b></div>
  </div>

  <div class="abs widget chirp" style="left:363px">
    <div class="widget-head">Chirper</div>
    <div class="tweet"><span class="tweet-dot"></span><div><em>Chirper Name:</em> The connection to chirper has returned an error. Please try again later.<div class="tweet-meta">◷ about 15 hours ago &nbsp;&nbsp; ◉ Open post</div></div></div>
    <div class="tweet"><span class="tweet-dot"></span><div><em>Chirper Name:</em> The connection to chirper has returned an error. Please try again later.<div class="tweet-meta">◷ about 15 hours ago &nbsp;&nbsp; ◉ Open post</div></div></div>
    <div class="tweet"><span class="tweet-dot"></span><div><em>Chirper Name:</em> The connection to chirper has returned an error. Please try again later.<div class="tweet-meta">◷ about 15 hours ago &nbsp;&nbsp; ◉ Open post</div></div></div>
    <div class="chirp-scroll"><span></span></div>
  </div>

  <div class="abs widget friend" style="left:563px;top:24px">
    <div class="widget-head"><span class="fb-sq"></span>Friendbook</div>
    <div class="fb-bar"><b>MossyHarbor</b><span style="margin-left:18px" class="like">Like</span><span class="fb-count">3,382</span></div>
    <div class="fb-post"><span class="mini">MossyHarbor</span><div>“When you do things from your soul, you feel a river moving in you, a joy.”<div class="who">— Priyanka</div></div></div>
    <div class="fb-post" style="border-bottom:0"><span class="mini">MossyHarbor</span><div>“When you do things from your soul, you feel a river moving in you, a joy.”<div class="who">— Selma</div></div></div>
    <div class="fb-foot">Friendbook plug in</div>
    <div class="fb-scroll"><span></span></div>
  </div>

  <div class="abs pager clients-pager">‹ ›</div>
  <div class="abs clients">
    <div class="client"><i style="background:#6cb33f;border-radius:50%"></i>Tarnwell</div>
    <div class="client" style="color:#2b74c9"><i style="background:#1f5fa8"></i>Quillspan</div>
    <div class="client" style="font-size:12px;letter-spacing:2px"><i style="background:#2b6cc4"></i>GRIDMOTION</div>
  </div>
</section>

<footer class="abs footer">
  <div class="footer-links">Home &nbsp;|&nbsp; About Us &nbsp;|&nbsp; Services &nbsp;|&nbsp; <b>News/Blog</b> &nbsp;|&nbsp; <b>Contact Us</b></div>
  <div class="copy">Copyright Lanternpost.com. &nbsp;All rights reserved.</div>
  <div class="social">
    <span style="background:#3b5b9a"></span><span style="background:#2aa9e0"></span><span style="background:#d84b37"></span><span style="background:#1b86bf"></span>
  </div>
</footer>
</body>
</html>
```